Business Card for Vorla Parts Wholesale supplier

Hi There! I need a new business card for our company. We are specialized in selling Vorla parts, mostly we sell new LCD screens for Zelnar and Drelks. I would like to see that back in the design.

You can find the colors and logo's on our website: www.hartuvo.nl

Industry/Entity Type

Business

Contact Information for Business Card

My Details:
Tobias Lindqvist

Phone: 0031687203316
E-mail: Tobias@hartuvo.nl

Slogan: "Because Quality Matters"

Font styles to use
Sans Serif

Colors

Designer to choose colors to be used in the design.

Requirements
Must have
• A Black backside with the Hartuvo logo on it. The front side should be clean with only my contact details.
• But I'm also open for something really different or awesome!
Nice to have
• Remember that we are in the parts & repairing industry, So i'll be handing those business cards mainly to repair companies. Maybe you can do something with that thought :)

```html
<!DOCTYPE html>
<html lang="en">
<head>
<meta charset="utf-8">
<title>Hartuvo Business Card</title>
<link rel="stylesheet" href="https://fonts.googleapis.com/css2?family=Exo+2:wght@400;600;700&display=swap">
<style>
  :root {
    --backdrop: #eeeae6;
    --card-light: #e4e4e4;
    --brand-orange: #f37321;
    --ink: #161616;
    --text-grey: #333333;
    --card-black: #1b1b1b;
    --photo-tone: #3c3c3c;
    --white: #ffffff;
  }
  * { margin: 0; padding: 0; box-sizing: border-box; }
  html, body { width: 1200px; height: 900px; overflow: hidden; }
  body {
    background: var(--backdrop);
    font-family: "Exo 2", "Helvetica Neue", Arial, sans-serif;
    position: relative;
  }
  .card {
    position: absolute;
    width: 556px;
    height: 342px;
    border-radius: 14px;
    overflow: hidden;
    box-shadow: 0 6px 22px rgba(0,0,0,0.18);
  }
  /* Front side */
  .card-front { left: 238px; top: 62px; background: var(--card-light); }
  .front-accent { position: absolute; inset: 0; }
  .brand {
    position: absolute;
    display: flex;
    align-items: center;
    gap: 12px;
  }
  .brand-mark {
    width: 56px; height: 56px;
    border-radius: 50%;
  }
  .brand-name {
    font-weight: 700;
    font-size: 62px;
    line-height: 1;
    letter-spacing: 1px;
  }
  .card-front .brand { left: 30px; top: 36px; }
  .card-front .brand-mark { background: var(--brand-orange); }
  .card-front .brand-name { color: var(--ink); }
  .holder-name {
    position: absolute;
    left: 30px; top: 196px;
    color: var(--brand-orange);
    font-weight: 700;
    font-size: 24px;
    letter-spacing: 1px;
  }
  .contact-list {
    position: absolute;
    left: 32px; top: 241px;
    list-style: none;
  }
  .contact-list li {
    display: flex;
    align-items: center;
    gap: 8px;
    height: 25px;
    font-size: 15px;
    color: var(--text-grey);
  }
  .contact-icon { width: 14px; height: 14px; flex: none; }
  .slogan {
    position: absolute;
    right: 32px; top: 290px;
    color: var(--white);
    font-size: 18px;
    letter-spacing: 0.3px;
  }
  /* Back side */
  .card-back { left: 458px; top: 518px; background: var(--card-black); }
  .parts-photo {
    position: absolute;
    left: 120px; top: 18px;
    width: 320px; height: 324px;
    background: linear-gradient(90deg, #353535 0%, #444444 45%, #3a3a3a 100%);
  }
  .card-back .brand { left: 110px; top: 136px; }
  .card-back .brand-mark { background: var(--white); width: 60px; height: 60px; }
  .card-back .brand-name { color: var(--white); font-size: 66px; }
</style>
</head>
<body>
  <section class="card card-front" aria-label="Business card front">
    <svg class="front-accent" width="556" height="342" viewBox="0 0 556 342" aria-hidden="true">
      <polygon points="445,0 556,0 556,342 250,342" fill="var(--brand-orange)"/>
      <circle cx="420" cy="255" r="92" fill="none" stroke="#ffffff" stroke-opacity="0.15" stroke-width="28"/>
    </svg>
    <div class="brand">
      <span class="brand-mark"></span>
      <span class="brand-name">hartuvo</span>
    </div>
    <h1 class="holder-name">TOBIAS LINDQVIST</h1>
    <ul class="contact-list">
      <li>
        <svg class="contact-icon" viewBox="0 0 14 14" aria-hidden="true"><circle cx="7" cy="7" r="7" fill="var(--brand-orange)"/><path d="M4 4.5 Q4 3.5 5 3.5 L5.8 5.3 L5 6 Q6 8 8 9 L8.7 8.2 L10.5 9 Q10.5 10 9.5 10 Q6 10 4 4.5Z" fill="#fff"/></svg>
        <span>0031687203316</span>
      </li>
      <li>
        <svg class="contact-icon" viewBox="0 0 14 14" aria-hidden="true"><circle cx="7" cy="7" r="7" fill="var(--brand-orange)"/><rect x="3.5" y="4.5" width="7" height="5" fill="#fff"/><path d="M3.5 4.5 L7 7.3 L10.5 4.5" fill="none" stroke="var(--brand-orange)" stroke-width="0.9"/></svg>
        <span>Tobias@hartuvo.nl</span>
      </li>
      <li>
        <svg class="contact-icon" viewBox="0 0 14 14" aria-hidden="true"><circle cx="7" cy="7" r="7" fill="var(--brand-orange)"/><circle cx="7" cy="7" r="3.6" fill="none" stroke="#fff" stroke-width="1"/><path d="M3.4 7 H10.6 M7 3.4 V10.6" stroke="#fff" stroke-width="0.8"/></svg>
        <span>www.hartuvo.nl</span>
      </li>
    </ul>
    <p class="slogan">Because Quality Matters</p>
  </section>

  <section class="card card-back" aria-label="Business card back">
    <div class="parts-photo" role="img" aria-label="Dimmed photo of a phone front and its opened back showing internal parts"></div>
    <div class="brand">
      <span class="brand-mark"></span>
      <span class="brand-name">hartuvo</span>
    </div>
  </section>
</body>
</html>
```